New Business card design to reflect rebrand

I would like a business card design with a good base colour for our new logo and also a placeholder for a profile pic of the card holder. the design needs to be editable to the point that we can easily change the picture of the person and use that design for printmerlo etc. we are looking at a metalic finish business card so will need a good base colour to bring out the finish.

Target Market(s)

prospective customers

Industry/Entity Type

Business

Contact Information for Business Card

I would like one editable design that we can change the name of the card holder and profile picture. The design need to be in a format that be send to printmerlo etc.

Our address is Fenwick Lodge, Copse Lane, Ashcombe Vale, GU14 3TP Tel no. 01483 556172

Requirements
Must have
• place holder for a profile pic for the card holder. in AI or preferably PSD format

```html
<!DOCTYPE html>
<html lang="en">
<head>
<meta charset="utf-8">
<title>Brackley Workplace Services – Business Card</title>
<link rel="stylesheet" href="https://fonts.googleapis.com/css2?family=Open+Sans:wght@400;600;700&family=Montserrat:wght@700;800&display=swap">
<style>
  :root {
    --bg: #e9e6e1;
    --card: #ffffff;
    --navy: #3e4b66;
    --orange: #f07a1c;
    --grey-text: #6b6b6b;
  }
  * { box-sizing: border-box; margin: 0; padding: 0; }
  html, body { width: 1200px; height: 950px; overflow: hidden; }
  body {
    background: var(--bg);
    font-family: "Open Sans", Arial, sans-serif;
    display: flex;
    align-items: center;
    justify-content: center;
    gap: 80px;
  }
  .card {
    width: 420px;
    height: 720px;
    background: var(--card);
    position: relative;
    box-shadow: 0 10px 30px rgba(0,0,0,0.18);
  }
  .card__frame {
    position: absolute;
    inset: 22px;
    border: 2px solid var(--navy);
  }
  .card--back .card__frame { border-color: var(--orange); }

  /* Front */
  .front__content {
    position: absolute;
    inset: 22px;
    display: flex;
    flex-direction: column;
    align-items: center;
    text-align: center;
  }
  .profile-photo {
    margin-top: 70px;
    width: 170px;
    height: 155px;
    border-radius: 12px;
    background: linear-gradient(180deg, #d3d3d3, #bdbdbd);
  }
  .holder-name {
    margin-top: 18px;
    font-weight: 700;
    font-size: 30px;
    letter-spacing: 1px;
    color: var(--navy);
  }
  .holder-role {
    font-size: 20px;
    font-weight: 400;
    color: var(--orange);
    letter-spacing: 0.5px;
  }
  .contact-icon { margin-top: 44px; }
  .address {
    margin-top: 10px;
    font-size: 17px;
    line-height: 1.3;
    color: var(--grey-text);
  }
  .phone-icon { margin-top: 34px; }
  .phone {
    margin-top: 8px;
    font-size: 17px;
    color: var(--grey-text);
    letter-spacing: 0.5px;
  }

  /* Back */
  .brand {
    position: absolute;
    top: 280px;
    left: 24px;
    right: 24px;
    display: flex;
    align-items: center;
    justify-content: center;
    gap: 12px;
  }
  .brand__mark {
    flex: 0 0 auto;
    width: 18px;
    height: 18px;
    background: var(--orange);
  }
  .brand__name {
    flex: 0 0 auto;
    font-family: "Montserrat", Arial, sans-serif;
    font-weight: 800;
    font-size: 24px;
    line-height: 1.2;
    color: var(--navy);
    letter-spacing: 1px;
    white-space: nowrap;
  }
  .website {
    position: absolute;
    bottom: 90px;
    left: 0;
    right: 0;
    text-align: center;
    font-size: 16px;
    letter-spacing: 3px;
    color: var(--grey-text);
  }
</style>
</head>
<body>
  <section class="card card--front">
    <div class="card__frame"></div>
    <div class="front__content">
      <div class="profile-photo" role="img" aria-label="Profile photo placeholder for the card holder"></div>
      <h1 class="holder-name">DANIEL HARPER</h1>
      <p class="holder-role">CEO/FOUNDER</p>
      <svg class="contact-icon" width="18" height="24" viewBox="0 0 18 24" aria-hidden="true">
        <path d="M9 0C4 0 0 4 0 9c0 6.5 9 15 9 15s9-8.5 9-15c0-5-4-9-9-9z" fill="var(--orange)"/>
        <circle cx="9" cy="9" r="3.5" fill="#fff"/>
      </svg>
      <p class="address">Fenwick Lodge<br>Copse Lane, Ashcombe Vale<br>GU14 3TP</p>
      <svg class="phone-icon" width="18" height="20" viewBox="0 0 18 20" aria-hidden="true">
        <path d="M4 1l3 4-2 2c1 3 3 5 6 7l2-2 4 3-2 4C8 18 1 10 1 3z" fill="var(--orange)"/>
      </svg>
      <p class="phone">01483 556172</p>
    </div>
  </section>

  <section class="card card--back">
    <div class="card__frame"></div>
    <div class="brand">
      <span class="brand__mark"></span>
      <span class="brand__name">BRACKLEY<br>WORKPLACE SERVICES</span>
    </div>
    <p class="website">www.brackleyws.com</p>
  </section>
</body>
</html>
```